We are a recruitment company based in Norwich/Cambridge England.
I have included our company logo which we want to remain the same.

What we are looking for is a new creative Business card which will really stand out!!

Contact Information for Business Card

Harriet Dunmore
email: Harriet@plavex.co.uk
Address: Brackwell House
Fenmoor Enterprise Park
Partridge Way
Norwich
QB9 3KX
Tel:01632 960418

```html
<!DOCTYPE html>
<html lang="en">
<head>
<meta charset="utf-8">
<title>Plavex Business Card</title>
<link href="https://fonts.googleapis.com/css2?family=Roboto:wght@400;500;700&display=swap" rel="stylesheet">
<style>
  :root {
    --bg: #2b2622;
    --card: #1d1f21;
    --card-edge: #26292b;
    --green: #7cc242;
    --grey: #8a8b8d;
    --white: #f2f2f2;
    --rule: #cfcfcf;
  }
  * { box-sizing: border-box; margin: 0; padding: 0; }
  html, body { width: 1200px; height: 769px; overflow: hidden; }
  body {
    background: var(--bg);
    font-family: "Roboto", Arial, sans-serif;
    position: relative;
  }
  .card {
    position: absolute;
    top: 224px;
    width: 530px;
    height: 303px;
    background: linear-gradient(135deg, var(--card-edge), var(--card));
    border-radius: 4px;
    box-shadow: 0 14px 30px rgba(0,0,0,.55);
  }
  .card--back { left: 50px; }
  .card--front { left: 620px; }

  /* back */
  .back-brand {
    position: absolute; left: 0; right: 0; top: 108px;
    text-align: center;
    font-size: 60px; font-weight: 700; color: var(--green);
    letter-spacing: 1px;
  }
  .back-web {
    position: absolute; left: 0; right: 0; top: 196px;
    text-align: center;
    font-size: 13px; color: var(--grey);
    letter-spacing: 6px;
  }

  /* front */
  .brand {
    position: absolute; left: 40px; top: 112px;
    display: flex; flex-direction: column;
  }
  .brand-row { display: flex; align-items: center; gap: 10px; }
  .brand-dot { width: 30px; height: 30px; border-radius: 50%; background: var(--green); }
  .brand-name { font-size: 46px; font-weight: 700; color: var(--green); line-height: 1; }
  .brand-tag {
    margin: 6px 0 0 42px;
    font-size: 9px; letter-spacing: 2px; color: var(--grey);
  }
  .divider {
    position: absolute; left: 262px; top: 40px;
    width: 1px; height: 222px;
    background: linear-gradient(to bottom, transparent, var(--rule) 30%, var(--rule) 70%, transparent);
  }
  .details { position: absolute; left: 284px; top: 52px; color: var(--white); }
  .name { font-size: 19px; font-weight: 700; color: var(--green); text-transform: uppercase; }
  .role { font-size: 14px; color: var(--grey); text-transform: uppercase; margin-bottom: 12px; }
  .address { font-size: 13px; line-height: 1.35; margin-bottom: 6px; }
  .contact { list-style: none; font-size: 13px; line-height: 1.5; }
  .contact li { display: flex; align-items: center; gap: 8px; }
  .contact svg { width: 12px; height: 12px; fill: var(--green); flex: none; }
  .contact .plain { padding-left: 20px; }
</style>
</head>
<body>
  <section class="card card--back">
    <div class="back-brand">Plavex</div>
    <div class="back-web">www.plavex.co.uk</div>
  </section>

  <section class="card card--front">
    <div class="brand">
      <div class="brand-row">
        <span class="brand-dot"></span>
        <span class="brand-name">Plavex</span>
      </div>
      <span class="brand-tag">technology Recruitment</span>
    </div>

    <div class="divider"></div>

    <div class="details">
      <p class="name">Harriet Dunmore</p>
      <p class="role">CEO/Founder</p>
      <p class="address">Brackwell House<br>Fenmoor Enterprise Park, QB9 3KX</p>
      <ul class="contact">
        <li><svg viewBox="0 0 12 12"><path d="M2 1h2.5l1 3-1.5 1a7 7 0 0 0 3 3l1-1.5 3 1V10a1 1 0 0 1-1 1A9 9 0 0 1 1 2a1 1 0 0 1 1-1z"/></svg>01632 960418</li>
        <li><svg viewBox="0 0 12 12"><path d="M3.5 0h5a1 1 0 0 1 1 1v10a1 1 0 0 1-1 1h-5a1 1 0 0 1-1-1V1a1 1 0 0 1 1-1zm.5 1.5v7.5h4V1.5z"/></svg>01632 960527</li>
        <li><svg viewBox="0 0 12 12"><path d="M1 3h10v7H1zM3 0h6v2.5H3zM3 5h6v1H3z"/></svg>07700 900184</li>
        <li><svg viewBox="0 0 12 12"><path d="M0 2h12v8H0zm1 1v.4l5 3.2 5-3.2V3z"/></svg>Harriet@plavex.co.uk</li>
        <li><svg viewBox="0 0 12 12"><path d="M6 0a6 6 0 1 0 0 12A6 6 0 0 0 6 0zm0 1.2a4.8 4.8 0 0 1 0 9.6 4.8 4.8 0 0 1 0-9.6zM3 4.5l2.5 1 1 2.5-2.5-1z"/></svg>www.plavex.co.uk</li>
      </ul>
    </div>
  </section>
</body>
</html>
```